Zolvana Stationary and Branding Documents

Corporate Identity Branding stationary needed for IT Recruiting Firm.

I already have a Logo, business cards and website. I need to get designs completed for the remaining corporate identity documents.

The documentation should use similar colors as my website and business card. The designs should modern and clean.

http://zolvanaworks.example/

Target Market(s)

Information Technology Industry

Industry/Entity Type

Information Technology

Colors
3377b5
0255a3
fbee3e
f78f20
f37122
33a6d7
000000
0592cd

Requirements
Must have
• Letter Head
• Folder Design
• PowerPoint Design
• Invoice
• Envelope
Nice to have
• Proposal
• Flyer
• Brochure
Should not have
• Logo
• Business Cards
• Website

```html
<!DOCTYPE html>
<html lang="en">
<head>
<meta charset="utf-8">
<title>Zolvana Letterhead</title>
<link rel="stylesheet" href="https://fonts.googleapis.com/css2?family=Open+Sans:wght@400;600;700&display=swap">
<style>
  :root {
    --backdrop: #b4c3f2;
    --paper: #f7f8f9;
    --brand-blue: #0255a3;
    --brand-orange: #f37122;
    --ink-black: #333333;
    --text-grey: #6b6f76;
    --rule-blue: #3377b5;
  }
  * { margin: 0; padding: 0; box-sizing: border-box; }
  html, body {
    width: 1200px;
    height: 784px;
    overflow: hidden;
  }
  body {
    background: var(--backdrop);
    font-family: "Open Sans", Arial, sans-serif;
    display: flex;
    align-items: center;
    justify-content: center;
  }
  .letterhead {
    position: relative;
    width: 523px;
    height: 740px;
    background: var(--paper);
    overflow: hidden;
    box-shadow: 0 6px 18px rgba(40, 60, 140, 0.18);
  }
  .brand-name {
    position: absolute;
    top: 34px;
    left: 38px;
    font-size: 34px;
    font-weight: 400;
    letter-spacing: 0.5px;
    color: var(--brand-blue);
    line-height: 1;
  }
  .header-rule {
    position: absolute;
    top: 62px;
    left: 182px;
    width: 303px;
    height: 1px;
    background: var(--rule-blue);
  }
  .contact-block {
    position: absolute;
    top: 150px;
    right: 38px;
    text-align: right;
    font-size: 7px;
    line-height: 1.6;
  }
  .contact-address {
    color: var(--brand-orange);
    font-weight: 700;
  }
  .contact-lines {
    color: var(--text-grey);
    display: flex;
    gap: 8px;
    justify-content: flex-end;
    align-items: center;
  }
  .contact-item {
    display: inline-flex;
    align-items: center;
    gap: 3px;
  }
  .contact-icon {
    width: 6px;
    height: 6px;
    fill: var(--brand-blue);
  }
  .footer-graphic {
    position: absolute;
    left: 0;
    bottom: 0;
    width: 523px;
    height: 200px;
  }
  .footer-url {
    position: absolute;
    right: 40px;
    bottom: 18px;
    color: #ffffff;
    font-size: 9px;
    font-weight: 600;
    letter-spacing: 0.2px;
  }
</style>
</head>
<body>
  <main class="letterhead">
    <div class="brand-name">zolvana</div>
    <div class="header-rule"></div>

    <div class="contact-block">
      <div class="contact-address">Two Harbor Plaza 410, 8th Avenue SE</div>
      <div class="contact-lines">
        <span class="contact-item">
          <svg class="contact-icon" viewBox="0 0 10 10"><path d="M2 0h2l1 3-1.5 1a6 6 0 0 0 2.5 2.5L7 5l3 1v2c0 1-1 2-2 2A8 8 0 0 1 0 2c0-1 1-2 2-2z"/></svg>
          5550148230
        </span>
        <span class="contact-item">
          <svg class="contact-icon" viewBox="0 0 10 10"><path d="M0 2h10v6H0z M0 2l5 3.5L10 2" fill="none" stroke="#0255a3" stroke-width="1.2"/></svg>
          info@zolvanaworks.example
        </span>
      </div>
    </div>

    <svg class="footer-graphic" viewBox="0 0 523 200" aria-hidden="true">
      <polygon class="band-black" points="0,0 0,200 300,200" fill="var(--ink-black)"/>
      <polygon class="band-orange" points="150,100 300,200 235,200" fill="var(--brand-orange)"/>
      <polygon class="band-blue" points="0,60 205,140 523,168 523,200 0,200" fill="var(--brand-blue)"/>
    </svg>
    <div class="footer-url">www.zolvanaworks.example</div>
  </main>
</body>
</html>
```